Modern Business Card

Modern professional business card with more than just logo and demographic info. Something memorable.

We are a trendy/modern chiropractic group with an emphasis on neurology, hence the minimalist-type brain logo. We want to convey that modern and technical aspect with professionalism and the elite nature of our practice environment.

```html
<!DOCTYPE html>
<html lang="en">
<head>
<meta charset="utf-8">
<title>Keystone Spine – Business Card</title>
<link href="https://fonts.googleapis.com/css2?family=Roboto:wght@400;700&display=swap" rel="stylesheet">
<style>
  :root{
    --bg:#d9dbde;
    --brand-blue:#3d78c4;
    --blue-deep:#3769bd;
    --blue-light:#5aaee0;
    --ink:#1d1d1f;
    --white:#ffffff;
    --line:#111111;
  }
  *{margin:0;padding:0;box-sizing:border-box;}
  html,body{width:1200px;height:960px;overflow:hidden;}
  body{background:var(--bg);font-family:'Roboto',Arial,sans-serif;position:relative;}

  .card{position:absolute;left:250px;width:700px;height:400px;border-radius:22px;overflow:hidden;
        box-shadow:0 10px 28px rgba(0,0,0,.22);}
  .card--back{top:50px;}
  .card--front{top:510px;background:var(--white);}

  .back-pattern{position:absolute;inset:0;
    background:linear-gradient(225deg,var(--blue-deep) 0%,var(--brand-blue) 55%,var(--blue-light) 100%);}
  .back-mark{position:absolute;right:70px;top:180px;width:44px;height:44px;border-radius:50%;background:var(--white);}

  .front-shape{position:absolute;inset:0;width:700px;height:400px;}

  .brand{position:absolute;left:200px;top:90px;display:flex;align-items:center;gap:14px;}
  .brand-dot{width:40px;height:40px;border-radius:50%;background:var(--brand-blue);}
  .brand-name{font-size:34px;font-weight:400;letter-spacing:2px;color:var(--ink);}

  .contact{position:absolute;right:30px;top:178px;list-style:none;text-align:right;color:var(--white);font-size:15px;line-height:21px;}
  .contact li{display:flex;justify-content:flex-end;align-items:center;gap:8px;}
  .contact svg{width:13px;height:13px;flex:none;}

  .person{position:absolute;left:40px;top:300px;color:var(--white);}
  .person-name{font-size:23px;font-weight:700;}
  .person-role{font-size:15px;font-weight:700;margin-top:2px;}
  .person-address{font-size:14px;line-height:19px;margin-top:10px;}
</style>
</head>
<body>

  <section class="card card--back" aria-label="Card back">
    <div class="back-pattern" role="img" aria-label="Repeating brand pattern in shades of blue"></div>
    <div class="back-mark"></div>
  </section>

  <section class="card card--front" aria-label="Card front">
    <svg class="front-shape" viewBox="0 0 700 400" aria-hidden="true">
      <path d="M0,262 L340,262 C355,262 360,255 362,240 L366,190 C368,170 376,162 396,162 L700,162 L700,400 L0,400 Z" fill="var(--brand-blue)"/>
      <path d="M0,252 L332,252 C346,252 351,246 353,232 L355,215" fill="none" stroke="var(--line)" stroke-width="5"/>
    </svg>

    <div class="brand">
      <span class="brand-dot"></span>
      <span class="brand-name">KEYSTONE SPINE</span>
    </div>

    <ul class="contact">
      <li>555-214-3087
        <svg viewBox="0 0 24 24"><path fill="#fff" d="M6.6 10.8a15 15 0 0 0 6.6 6.6l2.2-2.2c.3-.3.7-.4 1-.2 1.1.4 2.3.6 3.6.6.6 0 1 .4 1 1V20c0 .6-.4 1-1 1A17 17 0 0 1 3 4c0-.6.4-1 1-1h3.5c.6 0 1 .4 1 1 0 1.3.2 2.5.6 3.6.1.3 0 .7-.2 1z"/></svg></li>
      <li>555-630-1942
        <svg viewBox="0 0 24 24"><rect x="6" y="2" width="12" height="20" rx="2" fill="none" stroke="#fff" stroke-width="2"/><circle cx="12" cy="18" r="1.3" fill="#fff"/></svg></li>
      <li>555-478-2615
        <svg viewBox="0 0 24 24"><rect x="3" y="9" width="18" height="10" rx="1.5" fill="#fff"/><rect x="7" y="4" width="10" height="5" fill="#fff"/></svg></li>
      <li>name@keystonespine.com
        <svg viewBox="0 0 24 24"><rect x="2" y="5" width="20" height="14" rx="1.5" fill="#fff"/><path d="M2 6l10 7 10-7" fill="none" stroke="var(--brand-blue)" stroke-width="1.6"/></svg></li>
      <li>www.keystonespine.com
        <svg viewBox="0 0 24 24"><circle cx="12" cy="12" r="9" fill="none" stroke="#fff" stroke-width="2"/><path d="M3 12h18M12 3c3 3 3 15 0 18M12 3c-3 3-3 15 0 18" fill="none" stroke="#fff" stroke-width="1.6"/></svg></li>
    </ul>

    <div class="person">
      <p class="person-name">Daniel Reyes</p>
      <p class="person-role">President</p>
      <p class="person-address">4120 Birchwood Court<br>Juneau, Alaska 99801</p>
    </div>
  </section>

</body>
</html>
```